first fantastic look and impression

We are looking for a concept for letterhead, business card, emailfooter and template for invoices or offers for our company in the consultation business.
The dancer is a symbol who we are: it looks simple, but there is a lot of hard work and many years of training in this movement. The look is also what we want: elegant, modern, strong, with a touch of extravaganza
Target Market(s)
Hotelbusiness , Consulting
Font styles to use
Sans Serif
Other font styles liked:
- please give us a option we are open
Requirements
Must have
- We are not typical consultants but sparring partners and coaches for the hotel and that should also be expressed in the design. Maybe there is an icon that supports the whole thing. We are more modern and bolder than our industry colleagues.
we are modern, fresh, agile, fast
Nice to have
- a icon

```html
<!DOCTYPE html>
<html lang="en">
<head>
<meta charset="utf-8">
<title>Halvorsen+Partner – Letterhead</title>
<link href="https://fonts.googleapis.com/css2?family=Open+Sans:wght@400;700&display=swap" rel="stylesheet">
<style>
  :root{
    --backdrop:#d9dee1;
    --paper:#ffffff;
    --brand-blue:#5b7a9c;
    --brand-blue-dark:#3f5f86;
    --brand-gold:#e3c27d;
    --text-grey:#6d7780;
    --whisper:#eef0f2;
  }
  *{box-sizing:border-box;margin:0;padding:0}
  html,body{width:1200px;height:784px;overflow:hidden;background:var(--backdrop);font-family:"Open Sans",Arial,sans-serif}
  .letterhead{
    position:absolute;left:338px;top:22px;width:524px;height:740px;
    background:var(--paper);box-shadow:0 6px 18px rgba(60,70,80,.18);overflow:hidden;
  }
  .bar{position:absolute}
  .bar--blue{background:var(--brand-blue)}
  .bar--gold{background:var(--brand-gold)}

  .brand{position:absolute;left:34px;top:22px;width:240px}
  .brand__photo{
    width:92px;height:46px;border-radius:45% 55% 40% 60%;
    background:radial-gradient(ellipse at 40% 50%,#3e5878 0%,#5b7a9c 55%,rgba(91,122,156,0) 80%);
  }
  .brand__name{
    margin-top:8px;margin-left:58px;font-size:21px;font-weight:400;line-height:1.2;
    color:var(--brand-blue);letter-spacing:.3px;white-space:nowrap;
  }

  .contact{position:absolute;right:34px;top:62px;font-size:9.5px;line-height:14px;color:var(--text-grey);list-style:none}
  .contact li{display:flex;align-items:center;gap:4px;white-space:nowrap}
  .contact li:first-child{font-weight:700;color:var(--brand-blue-dark)}
  .contact svg{width:9px;height:9px;flex:none}

  .backdrop-figure{
    position:absolute;left:70px;top:230px;width:380px;height:390px;
    background:radial-gradient(ellipse at 50% 50%,var(--whisper) 0%,rgba(238,240,242,.7) 45%,rgba(255,255,255,0) 72%);
  }
</style>
</head>
<body>
<main class="letterhead">
  <!-- side accents near the top -->
  <div class="bar bar--gold" style="left:4px;top:19px;width:5px;height:34px"></div>
  <div class="bar bar--blue" style="left:0;top:61px;width:5px;height:35px"></div>
  <div class="bar bar--gold" style="right:4px;top:21px;width:5px;height:40px"></div>
  <div class="bar bar--blue" style="right:0;top:63px;width:5px;height:40px"></div>

  <header class="brand">
    <div class="brand__photo" role="img" aria-label="Small photograph of a dancer in a flowing blue dress"></div>
    <div class="brand__name">Halvorsen+Partner</div>
  </header>

  <ul class="contact">
    <li><svg viewBox="0 0 10 10"><circle cx="5" cy="5" r="5" fill="var(--brand-blue)"/><circle cx="5" cy="4.2" r="1.5" fill="#fff"/></svg>Brenndorf/Austria</li>
    <li><svg viewBox="0 0 10 10"><circle cx="5" cy="5" r="5" fill="var(--brand-blue)"/><rect x="2.5" y="3.3" width="5" height="3.4" fill="none" stroke="#fff" stroke-width=".8"/></svg>info@halvorsenpartner.com</li>
    <li><svg viewBox="0 0 10 10"><circle cx="5" cy="5" r="5" fill="var(--brand-blue)"/><circle cx="5" cy="5" r="2.4" fill="none" stroke="#fff" stroke-width=".8"/></svg>halvorsenpartner.com</li>
  </ul>

  <div class="backdrop-figure" role="img" aria-label="Faint large photograph of a dancer in a flowing dress as background decoration"></div>

  <!-- bottom edge bands -->
  <div class="bar bar--blue" style="left:0;bottom:0;width:377px;height:8px"></div>
  <div class="bar bar--gold" style="left:377px;bottom:0;width:147px;height:8px"></div>
  <div class="bar bar--gold" style="left:10px;bottom:12px;width:137px;height:3px"></div>
  <div class="bar bar--blue" style="left:152px;bottom:12px;width:175px;height:3px"></div>
  <div class="bar bar--gold" style="left:334px;bottom:12px;width:190px;height:3px"></div>
</main>
</body>
</html>
```